Corvane Freight Company Business Card Design

We are a company that delivers natural saltwater (from the ocean) to aquarium companies, restaurants and home marine tanks. I would like a new business card to suit.

Must include Name, company name, abn, contact number and website as well as logo (see attached).

Looking for a design that stands out, has a clean but unique appearance.

Double and single sided entries welcome

Business

• Logo

```html
<!DOCTYPE html>
<html lang="en">
<head>
<meta charset="utf-8">
<title>Corvane Freight Company – Business Card</title>
<link rel="stylesheet" href="https://fonts.googleapis.com/css2?family=Open+Sans:wght@400;600;700;800&family=Questrial&display=swap">
<style>
  :root {
    --backdrop: #1b1b1c;
    --backdrop-edge: #0f0f10;
    --deep-blue: #1462ef;
    --sea-blue: #42b3f6;
    --foam: #a9e1fb;
    --white: #ffffff;
  }
  * { margin: 0; padding: 0; box-sizing: border-box; }
  html, body {
    width: 1200px;
    height: 430px;
    overflow: hidden;
  }
  body {
    background: radial-gradient(ellipse at center, var(--backdrop) 40%, var(--backdrop-edge) 100%);
    position: relative;
    font-family: "Questrial", "Open Sans", sans-serif;
  }
  .card {
    position: absolute;
    top: 62px;
    width: 524px;
    height: 296px;
    border-radius: 24px;
    overflow: hidden;
    box-shadow: 0 6px 18px rgba(0, 0, 0, 0.55);
  }
  .card--front { left: 56px; background: var(--sea-blue); }
  .card--back { left: 627px; background: var(--sea-blue); }
  .card__waves { position: absolute; inset: 0; }
  .brand-name {
    position: absolute;
    left: 0;
    right: 0;
    text-align: center;
    font-family: "Open Sans", sans-serif;
    font-weight: 800;
    color: var(--white);
    letter-spacing: -0.5px;
    line-height: 1;
  }
  .card--front .brand-name { top: 70px; font-size: 40px; }
  .card--back .brand-name { top: 112px; font-size: 50px; }
  .holder {
    position: absolute;
    top: 160px;
    left: 0;
    right: 0;
    text-align: center;
    color: var(--white);
    font-family: "Open Sans", sans-serif;
  }
  .holder__name { font-weight: 700; font-size: 18px; }
  .holder__title { font-weight: 400; font-size: 14px; }
  .contact {
    position: absolute;
    top: 232px;
    color: var(--white);
    font-size: 13px;
    line-height: 19px;
  }
  .contact--address { right: 262px; text-align: right; }
  .contact--details { left: 286px; }
  .contact__divider {
    position: absolute;
    left: 274px;
    top: 232px;
    width: 1px;
    height: 58px;
    background: var(--white);
    opacity: 0.8;
  }
  .contact__row { display: flex; align-items: center; gap: 5px; }
  .contact__icon { width: 10px; height: 10px; flex: none; }
  .web-address {
    position: absolute;
    top: 246px;
    left: 0;
    right: 0;
    text-align: center;
    color: var(--white);
    font-size: 17px;
    letter-spacing: 3.5px;
  }
</style>
</head>
<body>

<section class="card card--front" aria-label="Business card front">
  <svg class="card__waves" width="524" height="296" viewBox="0 0 524 296" aria-hidden="true">
    <path d="M0 0 H524 V155 C400 165 300 205 190 203 C110 202 50 185 0 172 Z" fill="var(--deep-blue)"/>
    <path d="M0 172 C50 185 110 202 190 203 C300 205 400 165 524 155 L524 162 C400 176 300 214 190 213 C110 212 50 196 0 182 Z" fill="var(--foam)"/>
  </svg>

  <div class="brand-name">Corvane Freight</div>

  <div class="holder">
    <span class="holder__name">Your name,</span>
    <span class="holder__title">Title</span>
  </div>

  <address class="contact contact--address" style="font-style: normal;">
    Corvane Freight Company<br>
    Street Name, City Name<br>
    State, City Zip Code
  </address>

  <div class="contact__divider"></div>

  <div class="contact contact--details">
    <div class="contact__row">
      <svg class="contact__icon" viewBox="0 0 10 10" aria-hidden="true">
        <path d="M2 1 L4 1 L4.6 3 L3.4 4 C4 5.4 4.8 6.2 6 6.6 L7 5.4 L9 6 L9 8 C9 8.6 8.6 9 8 9 C4.2 9 1 5.8 1 2 C1 1.4 1.4 1 2 1 Z" fill="var(--white)"/>
      </svg>
      <span>123-456-7890</span>
    </div>
    <div class="contact__row">
      <svg class="contact__icon" viewBox="0 0 10 10" aria-hidden="true">
        <circle cx="5" cy="5" r="4.5" fill="var(--white)"/>
      </svg>
      <span>www.website.com</span>
    </div>
    <div class="contact__row">
      <span>ABN : 0123456789</span>
    </div>
  </div>
</section>

<section class="card card--back" aria-label="Business card back">
  <div class="brand-name">Corvane Freight</div>
  <div class="web-address">www.website.com</div>
</section>

</body>
</html>
```